Business Card Re-Design/Update

We'd like to update out business cards. I've included our current "Style guide" which has the colour scheme of the organisation in it. I've also included the branding files with logos etc in them.

I've also included a copy of one of our existing cards so that you can see how ugly/dated they look. I'd like a fresh modern corporate look.

Target Market(s)

These are for our clients, potential clients, industry contacts - like all business cards

Contact Information for Business Card

Name
Position
Company Address - Level 1, 47 Fernby Street, Carlow Qld 4072
Direct Phone
mobile
Email
Website -www.korvalit.com.au
Logo

Colors

Designer to choose colors to be used in the design.

Requirements
Must have
• Main Logo
• Cards will need to be editable to be able to personalize them for each new employee.
Nice to have
• The MapOut, ShipWell, KeepSteady would be okay to have if they can be sensibly and professionally added to the look without detracting from the main imagery.
• Maybe they could go on the back of the card? will leave this to your creative discretion as to whether/where they fit.
Should not have
• Should not have decorative or script fonts

```html
<!DOCTYPE html>
<html lang="en">
<head>
<meta charset="utf-8">
<title>Korvalit Business Card</title>
<link href="https://fonts.googleapis.com/css2?family=Roboto:wght@400;500;700&family=Roboto+Condensed:wght@400;700&display=swap" rel="stylesheet">
<style>
  :root {
    --backdrop: #e2e2e2;
    --card-white: #f7f7f7;
    --brand-red: #c8161d;
    --brand-red-deep: #9c0d12;
    --ink: #232323;
    --ink-soft: #4a4a4a;
    --faint-red: #f3e1e1;
  }
  * { margin: 0; padding: 0; box-sizing: border-box; }
  html, body { width: 1200px; height: 960px; overflow: hidden; }
  body { background: var(--backdrop); position: relative; font-family: "Roboto", sans-serif; }

  .card { position: absolute; width: 600px; height: 343px; overflow: hidden; box-shadow: 0 2px 4px rgba(0,0,0,.25); }

  /* Front */
  .card-front { left: 314px; top: 113px; background: var(--card-white); }
  .front-band { position: absolute; left: 0; top: 47px; width: 70px; height: 58px;
    background: linear-gradient(180deg, var(--brand-red), var(--brand-red-deep)); }
  .front-brand { position: absolute; left: 48px; top: 58px; display: flex; align-items: center; gap: 12px; }
  .brand-square { width: 36px; height: 36px; background: var(--brand-red); border: 3px solid var(--card-white); }
  .brand-name { font-weight: 700; font-size: 36px; color: var(--ink); letter-spacing: -0.5px; line-height: 1; }
  .faint-shape { position: absolute; right: -70px; top: 20px; width: 300px; height: 300px;
    background: var(--faint-red); transform: rotate(45deg); opacity: .7; }

  .holder { position: absolute; right: 36px; top: 55px; text-align: right; font-family: "Roboto Condensed", sans-serif; }
  .holder-name { font-weight: 700; font-size: 21px; color: var(--brand-red); letter-spacing: .3px; }
  .holder-role { font-size: 14.5px; color: var(--ink); margin-top: 2px; }

  .contact { position: absolute; left: 70px; top: 151px; list-style: none; font-size: 14.5px; color: var(--ink-soft); }
  .contact li { display: flex; align-items: flex-start; line-height: 19px; }
  .contact li.address { margin-bottom: 8px; }
  .contact svg { width: 12px; height: 12px; margin: 3px 12px 0 0; flex: none; fill: var(--brand-red); }

  /* Back */
  .card-back { left: 311px; top: 472px;
    background: linear-gradient(180deg, var(--brand-red) 0%, var(--brand-red-deep) 100%); color: #fff; }
  .back-brand { position: absolute; left: 0; right: 0; top: 118px; text-align: center;
    font-weight: 700; font-size: 54px; letter-spacing: -1px; }
  .services { position: absolute; left: 46px; right: 46px; top: 278px; display: flex; justify-content: space-between; list-style: none; }
  .service { display: flex; align-items: center; gap: 8px; font-weight: 500; font-size: 25px; }
  .service-mark { width: 22px; height: 22px; border: 3px solid #fff; transform: rotate(45deg); }
</style>
</head>
<body>
  <section class="card card-front" aria-label="Card front">
    <div class="faint-shape" aria-hidden="true"></div>
    <div class="front-band"></div>
    <div class="front-brand">
      <span class="brand-square"></span>
      <span class="brand-name">korvalit</span>
    </div>
    <div class="holder">
      <p class="holder-name">MAREN HOLT</p>
      <p class="holder-role">Business Development Manager</p>
    </div>
    <ul class="contact">
      <li class="address">
        <svg viewBox="0 0 12 12"><path d="M6 0a4.2 4.2 0 0 0-4.2 4.2C1.8 7.4 6 12 6 12s4.2-4.6 4.2-7.8A4.2 4.2 0 0 0 6 0zm0 5.8a1.6 1.6 0 1 1 0-3.2 1.6 1.6 0 0 1 0 3.2z"/></svg>
        <span>Level 1, 47 Fernby Street<br>Carlow QLD 4072</span>
      </li>
      <li><svg viewBox="0 0 12 12"><path d="M2.4 0l2 2.6-1.1 1.6c.8 1.8 2.2 3.3 4.4 4.5l1.6-1.1L12 9.6 10.3 12C4.8 11.4.6 7.2 0 1.7z"/></svg><span>+61 (0)7 3000 4120</span></li>
      <li><svg viewBox="0 0 12 12"><path d="M2.4 0l2 2.6-1.1 1.6c.8 1.8 2.2 3.3 4.4 4.5l1.6-1.1L12 9.6 10.3 12C4.8 11.4.6 7.2 0 1.7z"/></svg><span>+61 (0)7 3000 4127</span></li>
      <li><svg viewBox="0 0 12 12"><path d="M3 0h6a1 1 0 0 1 1 1v10a1 1 0 0 1-1 1H3a1 1 0 0 1-1-1V1a1 1 0 0 1 1-1zm.6 1.4v8h4.8v-8z"/></svg><span>+61 (0)400 555 318</span></li>
      <li><svg viewBox="0 0 12 12"><path d="M3 0h6v3H3zM0 4h12v5h-2v3H2V9H0zm3 4v3h6V8z"/></svg><span>+61 (0)7 3000 4199</span></li>
      <li><svg viewBox="0 0 12 12"><path d="M0 2h12v1L6 7 0 3zm0 2.4l6 4 6-4V10H0z"/></svg><span>mholt@korvalit.com.au</span></li>
      <li><svg viewBox="0 0 12 12"><circle cx="6" cy="6" r="6"/><path d="M3 3h3v2H4v2h2v2" fill="none" stroke="#f7f7f7" stroke-width="1"/></svg><span>www.korvalit.com.au</span></li>
    </ul>
  </section>

  <section class="card card-back" aria-label="Card back">
    <p class="back-brand">korvalit</p>
    <ul class="services">
      <li class="service"><span class="service-mark"></span>MapOut</li>
      <li class="service"><span class="service-mark"></span>ShipWell</li>
      <li class="service"><span class="service-mark"></span>KeepSteady</li>
    </ul>
  </section>
</body>
</html>
```